Birch And Harbor Website A Website design for book editing

A website design for book editing

Our proofreading, editing and manuscript review packages are specifically tailored to help you publish the best possible version of your story.

NEED HELP PUBLISHING A BESTSELLER?

If you’re looking for professional book editing services from senior publishing industry insiders, look no further. Besides editing, we can also answer all your publishing questions and get you started building your author platform.

OUR SERVICES

We've carefully structured our packages to maximize value for every budget.

PRICING

$.02
PER WORD
Proofreading
Line Edit (Copy-editing)
Fix spelling and grammar
Sales copy/summary revision

$.04
PER WORD
Proofreading
Line Edit (Copy-editing)
Fix spelling and grammar
Organization and content
Plot and pacing
Manuscript Review

$.06
PER WORD
Proofreading
Line Edit (Copy-editing)
Fix spelling and grammar
Organization and content
Plot and pacing
Manuscript Review
Formatting (print and ebook)
Pre-publication proofread

OUR PROCESS

Send us a sample of your book. Our caffeine-fueled, eagle-eyed editors will go through it and then email you with their comments and suggestions. You can ask them any questions you want. They will look for…

Typos and grammatical errors.
Spelling and word choice issues
Punctuation and style
Word choice, clarity and flow.
Sentence structure and craft
If your writing is already clean, then they’ll discuss bigger picture things with you, like theme, concept, purpose, audience, potential market and branding (including title, subtitle, and tagline or elevator pitch).

Once you feel comfortable and confident in an editor’s expertise, skill and knowledge, and are ready to move ahead, we’ll send an invoice for the first half of the total word count so the editor can get started. We’ll charge the rest when the project is close to completion.

Target Market(s)

Authors

Industry/Entity Type

Book Publisher

Coding

Coded - Design and coding required

Number of Pages Required

1 page

Requirements
Must have
• OUR SERVICES
• We've carefully structured our packages to maximize value for every budget.
• PRICING
• $.02
• PER WORD
• Proofreading
• Line Edit (Copy-editing)
• Fix spelling and grammar
• Sales copy/summary revision
• $.04
• PER WORD
• Proofreading
• Organization and content
• Plot and pacing
• Manuscript Review
• $.06
• PER WORD
• Proofreading
• Plot and pacing
• Manuscript Review
• Formatting (print and ebook)
• Pre-publication proofread

```html
<!DOCTYPE html>
<html lang="en">
<head>
<meta charset="utf-8">
<title>Birch And Harbor – Book Editing</title>
<link rel="stylesheet" href="https://fonts.googleapis.com/css2?family=Montserrat:wght@400;600;700;800&family=Open+Sans:wght@400;600;700&display=swap">
<style>
:root{
  --red:#c1121f;
  --red-dark:#a10e19;
  --ink:#1f1f1f;
  --text:#555;
  --muted:#8a8a8a;
  --line:#e4e4e4;
  --panel:#ffffff;
  --grey-bg:#e9e9e9;
  --grey-deep:#cfcfcf;
  --dark-card:#4d4d4f;
  --teal-card:#a7d6da;
  --teal-badge:#7fb7bd;
  --orange-badge:#d9822b;
  --soft-bg:#f2f1f1;
  --footer-bg:#f7f7f7;
}
*{box-sizing:border-box;margin:0;padding:0}
html,body{width:1200px;height:4138px;overflow:hidden}
body{font-family:"Open Sans",Arial,sans-serif;color:var(--text);background:#fff;position:relative}
.heading{font-family:"Montserrat",Arial,sans-serif;font-weight:700;color:var(--ink);text-align:center;letter-spacing:.5px}

/* header */
.site-header{position:absolute;top:0;left:0;width:1200px;height:102px;background:#fff}
.brand{position:absolute;left:130px;top:22px;font-family:"Montserrat",Arial,sans-serif;font-weight:700;font-size:30px;color:var(--red);display:flex;align-items:center;gap:10px}
.brand-dot{width:14px;height:14px;border-radius:50%;background:var(--red)}
.contact-strip{position:absolute;right:130px;top:20px;display:flex;gap:40px}
.contact-item{display:flex;align-items:center;gap:10px;font-size:12px;color:var(--ink)}
.contact-item small{display:block;font-size:9px;color:var(--muted);letter-spacing:.5px}
.contact-item b{font-weight:600;font-size:13px}
.main-nav{position:absolute;right:130px;top:66px;display:flex;gap:30px;font-family:"Montserrat",Arial,sans-serif;font-weight:700;font-size:13px;color:var(--ink)}
.main-nav a{color:inherit;text-decoration:none;padding-bottom:6px}
.main-nav a.active{color:var(--red);border-bottom:2px solid var(--red)}

/* hero */
.hero{position:absolute;top:102px;left:0;width:1200px;height:588px;background:linear-gradient(120deg,#5d5a55 0%,#a8a39b 35%,#d8d3cb 60%,#8d8880 100%)}
.hero-title{position:absolute;top:148px;width:100%;text-align:center;font-family:"Montserrat",Arial,sans-serif;font-weight:800;font-size:40px;line-height:50px;color:#fff;letter-spacing:.5px}
.hero-arrow{position:absolute;top:270px;width:36px;height:44px;background:rgba(20,20,20,.75);display:flex;align-items:center;justify-content:center}
.hero-arrow.prev{left:0}.hero-arrow.next{right:0}

/* services */
.services{position:absolute;top:690px;left:0;width:1200px;height:745px;background:linear-gradient(#fff 0%,#fff 52%,var(--grey-bg) 70%,#dcdcdc 100%)}
.services .heading{position:absolute;top:64px;width:100%;font-size:20px}
.section-sub{position:absolute;top:108px;width:100%;text-align:center;font-size:14px}
.service-card{position:absolute;left:180px;top:198px;width:840px;height:540px;background:var(--panel);box-shadow:0 4px 20px rgba(0,0,0,.12);display:grid;grid-template-columns:repeat(3,1fr);grid-template-rows:repeat(2,1fr);padding:40px 40px 30px}
.service{text-align:center;padding:18px 30px 0;border-right:1px solid var(--line)}
.service:nth-child(3n){border-right:0}
.service:nth-child(-n+3){border-bottom:1px solid var(--line)}
.service svg{display:block;margin:0 auto 22px}
.service h3{font-family:"Montserrat",Arial,sans-serif;font-size:15px;font-weight:600;color:var(--ink);margin-bottom:12px}
.service p{font-size:11.5px;line-height:16px;color:var(--muted)}

/* pricing */
.pricing{position:absolute;top:1435px;left:0;width:1200px;height:705px;background:linear-gradient(#dcdcdc 0%,#e6e6e6 55%,#f0f0f0 56%,#e3e3e3 100%)}
.pricing .heading{position:absolute;top:72px;width:100%;font-size:20px}
.plan{position:absolute;top:155px;width:272px;background:#fff;box-shadow:0 4px 16px rgba(0,0,0,.15);text-align:center;padding-bottom:30px}
.plan-basic{left:157px}.plan-standard{left:459px}.plan-premium{left:761px}
.plan-head{height:160px;position:relative;clip-path:polygon(0 0,100% 0,100% 75%,50% 100%,0 75%);padding-top:26px}
.plan-basic .plan-head{background:var(--dark-card)}
.plan-standard .plan-head{background:var(--red)}
.plan-premium .plan-head{background:var(--teal-card)}
.price{font-family:"Montserrat",Arial,sans-serif;font-size:40px;font-weight:600;color:#fff}
.price sup{font-size:18px;vertical-align:18px;margin-right:2px}
.plan-premium .price{color:var(--ink)}
.per-word{display:inline-block;margin-top:8px;padding:5px 22px;font-family:"Montserrat",Arial,sans-serif;font-size:11px;font-weight:700;color:#fff}
.plan-basic .per-word{background:#7b7b7d}
.plan-standard .per-word{background:var(--orange-badge)}
.plan-premium .per-word{background:var(--teal-badge)}
.features{list-style:none;margin:28px 28px 24px}
.features li{font-size:12px;color:var(--ink);line-height:24px;border-bottom:1px solid var(--line)}
.btn{display:inline-block;background:var(--red);color:#fff;font-family:"Montserrat",Arial,sans-serif;font-weight:700;font-size:12px;padding:8px 18px;border-radius:3px;text-decoration:none}

/* process */
.process{position:absolute;top:2140px;left:0;width:1200px;height:703px;background:#fff}
.process .heading{position:absolute;top:100px;width:100%;font-size:20px}
.process-intro{position:absolute;top:152px;left:350px;width:500px;text-align:center;font-size:13px;line-height:20px}
.process-path{position:absolute;top:280px;left:0}
.step{position:absolute;top:300px;width:180px;text-align:center;margin-left:-90px}
.step svg{display:block;margin:0 auto}
.step h4{margin-top:26px;font-size:13px;font-weight:600;color:var(--ink);line-height:18px}
.step .num{font-family:"Montserrat",Arial,sans-serif;font-size:48px;font-weight:400;color:#d4d4d4;margin-top:6px}
.process .btn{position:absolute;top:574px;left:556px}

/* testimonials */
.testimonials{position:absolute;top:2843px;left:0;width:1200px;height:510px;background:var(--soft-bg)}
.testimonial-art{position:absolute;left:55px;top:42px;width:510px;height:418px;background:linear-gradient(160deg,#eaf0f4 0%,#c9d3da 45%,#e4773a 80%,#f2f1f1 100%);border-radius:4px}
.testimonials h2{position:absolute;left:630px;top:80px;font-family:"Montserrat",Arial,sans-serif;font-size:19px;font-weight:700;color:var(--ink)}
.quote-mark{position:absolute;font-family:Georgia,serif;font-size:60px;color:#bbb;line-height:1}
.quote-open{left:600px;top:150px}.quote-close{left:755px;top:330px}
.testimonials blockquote{position:absolute;left:645px;top:200px;width:440px;font-size:13px;line-height:21px;color:var(--text)}
.reviewer{position:absolute;left:635px;top:398px;font-size:11px;color:var(--ink)}
.reviewer b{display:block;font-weight:700}
.reviewer::before{content:"";display:block;width:48px;height:1px;background:#999;margin-bottom:10px}
.dots{position:absolute;left:920px;top:442px;display:flex;gap:10px}
.dots span{width:8px;height:8px;border-radius:50%;background:#b8b8b8}
.dots span.on{background:#7aa6a8}

/* call to action */
.cta{position:absolute;top:3353px;left:0;width:1200px;height:400px;background:linear-gradient(100deg,#3c3c3c 0%,#5a5a5a 50%,#444 100%);text-align:center;color:#fff}
.cta h2{margin-top:116px;font-family:"Montserrat",Arial,sans-serif;font-size:21px;font-weight:700}
.cta p{width:640px;margin:10px auto 0;font-size:15px;line-height:22px}
.cta .btn{margin-top:28px;font-size:15px;padding:14px 26px}

/* footer */
.site-footer{position:absolute;top:3753px;left:0;width:1200px;height:385px;background:var(--footer-bg)}
.footer-brand{position:absolute;left:135px;top:135px;font-family:"Montserrat",Arial,sans-serif;font-weight:700;font-size:36px;color:var(--red)}
.footer-col{position:absolute;top:74px;font-size:11px;color:var(--ink)}
.footer-col h5{font-family:"Montserrat",Arial,sans-serif;font-size:11px;font-weight:700;color:var(--red);margin-bottom:16px;letter-spacing:.5px}
.footer-col li{list-style:none;line-height:16px}
.col-contact{left:552px}.col-menu{left:765px}.col-social{left:930px}
.contact-line{display:flex;gap:12px;margin-bottom:18px;line-height:16px}
.social-line{display:flex;align-items:center;gap:10px;margin-bottom:14px}
.social-line i{width:24px;height:24px;border-radius:50%;background:#1f3a5f;display:block}
.footer-rule{position:absolute;left:135px;top:282px;width:930px;height:1px;background:var(--line)}
.copyright{position:absolute;top:330px;width:100%;text-align:center;font-size:11px;color:var(--text)}
</style>
</head>
<body>

<header class="site-header">
  <div class="brand"><span class="brand-dot"></span>Birch And Harbor</div>
  <div class="contact-strip">
    <div class="contact-item">
      <svg width="18" height="14" viewBox="0 0 18 14"><rect x="1" y="1" width="16" height="12" fill="none" stroke="#1f1f1f" stroke-width="1.6"/><path d="M1 1l8 7 8-7" fill="none" stroke="#1f1f1f" stroke-width="1.6"/></svg>
      <div><small>E-MAIL US</small><b>info@birchandharbor.com</b></div>
    </div>
    <div class="contact-item">
      <svg width="16" height="16" viewBox="0 0 16 16"><path d="M3 1l3 3-2 2c1 2 3 4 5 5l2-2 3 3-2 3C7 15 1 9 1 3z" fill="#1f1f1f"/></svg>
      <div><small>CALL US</small><b>555.014.2290</b></div>
    </div>
  </div>
  <nav class="main-nav">
    <a class="active" href="#">HOME</a><a href="#">ABOUT US</a><a href="#">SERVICES</a><a href="#">PRICING</a><a href="#">TESTIMONIALS</a><a href="#">CONTACT US</a>
  </nav>
</header>

<section class="hero" role="img" aria-label="Photograph of hands writing in a notebook beside a laptop on a desk">
  <h1 class="hero-title">NEED HELP PUBLISHING<br>A BESTSELLER?</h1>
  <span class="hero-arrow prev"><svg width="10" height="14" viewBox="0 0 10 14"><path d="M8 1L2 7l6 6" fill="none" stroke="#fff" stroke-width="2"/></svg></span>
  <span class="hero-arrow next"><svg width="10" height="14" viewBox="0 0 10 14"><path d="M2 1l6 6-6 6" fill="none" stroke="#fff" stroke-width="2"/></svg></span>
</section>

<section class="services">
  <h2 class="heading">OUR SERVICES</h2>
  <p class="section-sub">We've carefully structured our packages to maximize value for every budget.</p>
  <div class="service-card">
    <div class="service">
      <svg width="50" height="50" viewBox="0 0 50 50"><rect x="8" y="8" width="30" height="34" fill="none" stroke="#c1121f" stroke-width="3"/><path d="M14 18h18M14 25h18M14 32h10" stroke="#c1121f" stroke-width="3"/><path d="M30 40l14-14" stroke="#c1121f" stroke-width="4"/></svg>
      <h3>Copy Editing</h3>
      <p>Careful line edits that tighten every sentence and keep your voice clear.</p>
    </div>
    <div class="service">
      <svg width="56" height="50" viewBox="0 0 56 50"><rect x="4" y="6" width="48" height="30" fill="none" stroke="#c1121f" stroke-width="3"/><path d="M10 28l10-10 8 6 10-12 8 8" fill="none" stroke="#c1121f" stroke-width="3"/><path d="M22 44h12M28 36v8" stroke="#c1121f" stroke-width="3"/></svg>
      <h3>Developmental Editing</h3>
      <p>Big picture feedback on structure, character and pacing before the final draft.</p>
    </div>
    <div class="service">
      <svg width="56" height="50" viewBox="0 0 56 50"><path d="M28 12C20 6 10 6 4 8v32c6-2 16-2 24 4 8-6 18-6 24-4V8c-6-2-16-2-24 4z" fill="none" stroke="#c1121f" stroke-width="3"/><path d="M28 12v32" stroke="#c1121f" stroke-width="3"/></svg>
      <h3>Book Evaluations</h3>
      <p>An honest reader report on strengths, weak spots and market potential today.</p>
    </div>
    <div class="service">
      <svg width="50" height="50" viewBox="0 0 50 50"><rect x="6" y="6" width="38" height="38" fill="none" stroke="#c1121f" stroke-width="3"/><rect x="12" y="12" width="12" height="12" fill="#c1121f"/><path d="M28 14h10M28 20h10M12 30h26M12 36h26" stroke="#c1121f" stroke-width="3"/></svg>
      <h3>Book Design and Layout</h3>
      <p>Clean interior layouts and covers prepared for print runs and ebook stores.</p>
    </div>
    <div class="service">
      <svg width="44" height="50" viewBox="0 0 44 50"><rect x="6" y="4" width="30" height="42" fill="#c1121f"/><path d="M12 14h18M12 20h18" stroke="#fff" stroke-width="2.5"/><rect x="36" y="10" width="4" height="8" fill="#c1121f"/></svg>
      <h3>Book Indexing</h3>
      <p>Thorough indexes that help readers find names, topics and terms with ease.</p>
    </div>
    <div class="service">
      <svg width="56" height="50" viewBox="0 0 56 50"><path d="M4 6h30v20H16l-8 7v-7H4z" fill="#c1121f"/><path d="M22 20h30v20h-4v7l-8-7H22z" fill="#c1121f" stroke="#fff" stroke-width="2"/><circle cx="30" cy="30" r="2" fill="#fff"/><circle cx="37" cy="30" r="2" fill="#fff"/><circle cx="44" cy="30" r="2" fill="#fff"/></svg>
      <h3>Writing and Publishing Advice</h3>
      <p>Straight answers on agents, platforms and self publishing from seasoned industry insiders.</p>
    </div>
  </div>
</section>

<section class="pricing">
  <h2 class="heading">PRICING</h2>
  <div class="plan plan-basic">
    <div class="plan-head"><div class="price"><sup>$</sup>.02</div><span class="per-word">PER WORD</span></div>
    <ul class="features"><li>Proofreading</li><li>Line Edit (Copy-editing)</li><li>Fix spelling and grammar</li><li>Sales copy/summary revision</li></ul>
    <a class="btn" href="#">Get Started</a>
  </div>
  <div class="plan plan-standard">
    <div class="plan-head"><div class="price"><sup>$</sup>.04</div><span class="per-word">PER WORD</span></div>
    <ul class="features"><li>Proofreading</li><li>Line Edit (Copy-editing)</li><li>Fix spelling and grammar</li><li>Sales copy/summary revision</li><li>Organization and content</li><li>Plot and pacing</li><li>Manuscript Review</li></ul>
    <a class="btn" href="#">Get Started</a>
  </div>
  <div class="plan plan-premium">
    <div class="plan-head"><div class="price"><sup>$</sup>.06</div><span class="per-word">PER WORD</span></div>
    <ul class="features"><li>Proofreading</li><li>Line Edit (Copy-editing)</li><li>Fix spelling and grammar</li><li>Sales copy/summary revision</li><li>Organization and content</li><li>Plot and pacing</li><li>Manuscript Review</li><li>Formatting (print and ebook)</li><li>Pre-publication proofread</li></ul>
    <a class="btn" href="#">Get Started</a>
  </div>
</section>

<section class="process">
  <h2 class="heading">OUR PROCESS</h2>
  <p class="process-intro">Send us a sample of your book. Our caffeine-fueled, eagle-eyed editors will go through it and then email you with their comments and suggestions. You can ask them any questions you want. They will look for…</p>
  <svg class="process-path" width="1200" height="80" viewBox="0 0 1200 80">
    <g fill="none" stroke="#555" stroke-width="1.5" stroke-dasharray="3 5">
      <path d="M240 30 C280 -10 340 -10 380 20"/>
      <path d="M440 50 C480 80 540 80 580 45"/>
      <path d="M640 25 C680 -10 740 -10 780 20"/>
      <path d="M840 50 C880 80 940 80 980 45"/>
    </g>
  </svg>
  <div class="step" style="left:201px">
    <svg width="56" height="50" viewBox="0 0 56 50"><text x="2" y="40" font-family="Montserrat,Arial,sans-serif" font-weight="800" font-size="34" fill="#2b2b2b">Aa</text><path d="M40 6l10 10" stroke="#2b2b2b" stroke-width="3"/></svg>
    <h4>Typos and<br>grammatical errors</h4><div class="num">01</div>
  </div>
  <div class="step" style="left:408px">
    <svg width="44" height="50" viewBox="0 0 44 50"><rect x="6" y="6" width="32" height="40" fill="none" stroke="#2b2b2b" stroke-width="3"/><rect x="15" y="2" width="14" height="8" fill="#2b2b2b"/><path d="M12 20h20M12 27h20M12 34h14" stroke="#2b2b2b" stroke-width="2.5"/></svg>
    <h4>Spelling and<br>word choice issues</h4><div class="num">02</div>
  </div>
  <div class="step" style="left:602px">
    <svg width="50" height="50" viewBox="0 0 50 50"><rect x="4" y="6" width="34" height="38" fill="none" stroke="#2b2b2b" stroke-width="3"/><path d="M10 16h14M10 24h14M10 32h22" stroke="#2b2b2b" stroke-width="2.5"/><path d="M28 30l16-16 4 4-16 16h-4z" fill="#2b2b2b"/></svg>
    <h4>Punctuation<br>and style</h4><div class="num">03</div>
  </div>
  <div class="step" style="left:800px">
    <svg width="40" height="50" viewBox="0 0 40 50"><path d="M4 2h22l10 10v36H4z" fill="#2b2b2b"/><path d="M26 2v10h10" fill="#777"/><path d="M10 24h20M10 31h20M10 38h14" stroke="#fff" stroke-width="2.5"/></svg>
    <h4>Word choice,<br>clarity and flow</h4><div class="num">04</div>
  </div>
  <div class="step" style="left:1007px">
    <svg width="50" height="44" viewBox="0 0 50 44"><rect x="2" y="6" width="18" height="14" fill="#2b2b2b"/><path d="M24 8h24M24 16h24M2 26h46M2 34h46" stroke="#2b2b2b" stroke-width="3"/></svg>
    <h4>Sentence<br>structure and craft</h4><div class="num">05</div>
  </div>
  <a class="btn" href="#">Read More</a>
</section>

<section class="testimonials">
  <div class="testimonial-art" role="img" aria-label="Illustration of hands typing on a laptop with a chat bubble"></div>
  <h2>TESTIMONIALS</h2>
  <span class="quote-mark quote-open">“</span>
  <blockquote>On the other hand, we denounce with righteous indignation and dislike men who are so beguiled and demoralized by the charms of pleasure of the moment, so blinded by desire, that they cannot foresee the pain and trouble that are bound to ensue; and equal blame belongs to those who fail in their duty through weakness.</blockquote>
  <span class="quote-mark quote-close">”</span>
  <div class="reviewer"><b>HOWARD</b>Scotland</div>
  <div class="dots"><span class="on"></span><span></span><span></span><span></span><span></span></div>
</section>

<section class="cta" role="img" aria-label="Dark photograph of a hand writing on paper">
  <h2>LOREM IPSUM IS SIMPLY DUMMY TEXT OF THE PRINTING.</h2>
  <p>On the other hand, we denounce with righteous indignation and dislike men who are so beguiled and demoralized by the charms of pleasure of the moment.</p>
  <a class="btn" href="#">Edit Your Book</a>
</section>

<footer class="site-footer">
  <div class="footer-brand">Birch And Harbor</div>
  <div class="footer-col col-contact">
    <h5>CONTACT US</h5>
    <div class="contact-line"><svg width="10" height="14" viewBox="0 0 10 14"><path d="M5 0a5 5 0 0 1 5 5c0 4-5 9-5 9S0 9 0 5a5 5 0 0 1 5-5z" fill="#1f1f1f"/><circle cx="5" cy="5" r="2" fill="#fff"/></svg><span>218 Lantern Avenue<br>Maple Ridge, IL 60400</span></div>
    <div class="contact-line"><svg width="12" height="12" viewBox="0 0 16 16"><path d="M3 1l3 3-2 2c1 2 3 4 5 5l2-2 3 3-2 3C7 15 1 9 1 3z" fill="#1f1f1f"/></svg><span>555.014.2290</span></div>
    <div class="contact-line"><svg width="13" height="10" viewBox="0 0 18 14"><rect x="0" y="0" width="18" height="14" fill="#1f1f1f"/><path d="M1 1l8 6 8-6" fill="none" stroke="#fff" stroke-width="1.5"/></svg><span>info@birchandharbor.com</span></div>
  </div>
  <div class="footer-col col-menu">
    <h5>MENU</h5>
    <ul><li>Home</li><li>About Us</li><li>Services</li><li>Pricing</li><li>Testimonials</li><li>Contact Us</li></ul>
  </div>
  <div class="footer-col col-social">
    <h5>CONNECT WITH US</h5>
    <div class="social-line"><i></i>Pageboard</div>
    <div class="social-line"><i></i>Chirpline</div>
    <div class="social-line"><i></i>Linkfold</div>
  </div>
  <div class="footer-rule"></div>
  <p class="copyright">Copyrights @ 2018 All Rights Reserved</p>
</footer>

</body>
</html>
```